Creation of a Velmaro website

Velmaro is a company% 26 # 233; t% 26 # 233; consulting that accompanies Swiss companies or% 26 # 233; strang% 26 # 232; res in the d% 26 # 233; development of their business on the market% 26 # 233; Switzerland by providing strategic contacts (personalized contact program% 26 # 233; s) or market information% 26 # 233; (% 26 # 233; market research% 26 # 233;) and by providing administrative support (repr% 26 # 233; tax representation) or logistics (organization of% 26 # 233; v% 26 # 233; nement, assistance for participation% 26 # 224; fairs). Our customers are mainly European companies wishing to develop their business in Switzerland. N% 26 # 233; however, our services are% 26 # 233; also aimed at Swiss companies wishing to develop in other parts of Switzerland. Our site must therefore be% 26 # 234; capable of being translated into several languages. The services offered% 26 # 233; s by Velmaro may also% 26 # 233; also% 26 # 39;% 26 # 233; tender% 26 # 224; promoting tourism in Switzerland for countries or regions% 26 # 233; foreigners or% 26 # 224; the promotion of trade fairs or fairs with% 26 # 232; sd% 26 # 39; companies of the sectors concerned% 26 # 233; s. It is therefore n% 26 # 233; necessary to be able to add sub-headings of services which can% 26 # 234; be displayed% 26 # 233; es or hide% 26 # 233; es as required. We are 2 associates% 26 # 233; s, low% 26 # 233; s in the French-speaking parts (Neuch% 26 # 226; tel) and al% 26 # 233; manique (Zurich) of Switzerland.

Target Market(s)

Swiss or European companies wishing to develop their activities in Switzerland.

Coding

Coded - Design and coding required

Colors

Designer to choose colors to be used in the design.

Requirements
Must have
• A home page A section of% 26 # 233; writing the services offered% 26 # 233; es by Velmaro with the possibility% 26 # 233; d% 26 # 39; add sub-headings which can% 26 # 234; be displayed% 26 # 233; e or hidden% 26 # 233; e A page with the r% 26 # 233; f% 26 # 233; which can be displayed% 26 # 233; e or hidden% 26 # 233; e A page of% 26 # 233; writing l% 26 # 39;% 26 # 233; team A page with form contact, addresses and int card% 26 # 233; gr% 26 # 233; e The site must% 26 # 234; be low% 26 # 233; on a CMS allowing% 26 # 39;% 26 # 234; to be autonomous in modifying the website The possibility% 26 # 233; to be able to translate the site into several languages (FR, EN, DE, IT, NL, ...)

```html
<!DOCTYPE html>
<html lang="en">
<head>
<meta charset="utf-8">
<title>Velmaro</title>
<link href="https://fonts.googleapis.com/css2?family=Lato:wght@400;700;900&display=swap" rel="stylesheet">
<style>
:root{
  --navy:#1c3347;
  --navy-deep:#16273a;
  --heading:#2f3d48;
  --service-title:#2f4f63;
  --text:#4a4a4a;
  --muted:#5f6770;
  --icon-grey:#8f99a4;
  --frame:#8d9aae;
  --ring:#b3bcc8;
  --send:#8b9ab0;
  --white:#ffffff;
}
*{box-sizing:border-box;margin:0;padding:0}
html,body{width:1200px;height:2887px;overflow:hidden;background:var(--white);font-family:'Lato',sans-serif;color:var(--text)}
.page{position:relative;width:1200px;height:2887px}
.abs{position:absolute}

/* header */
.site-header{position:absolute;left:0;top:0;width:1200px;height:107px;background:var(--white)}
.brand{position:absolute;left:75px;top:35px;display:flex;align-items:center;gap:22px}
.brand-mark{width:43px;height:43px;border-radius:8px;background:var(--navy)}
.brand-name{font-size:34px;font-weight:400;letter-spacing:3px;color:var(--navy)}
.nav{position:absolute;top:38px;left:451px;height:38px;font-size:14px;font-weight:700;color:var(--heading)}
.nav a{text-decoration:none;color:inherit}
.nav .active{background:var(--navy);color:var(--white);padding:0 17px;height:38px;line-height:38px}
.nav-item{position:absolute;top:0;line-height:38px;white-space:nowrap}
.lang{color:#8a929b;font-weight:700}

/* hero */
.hero{position:absolute;left:0;top:107px;width:1200px;height:673px;background:linear-gradient(120deg,#8c9bbd 0%,#a9b3cc 35%,#8995b5 60%,#6f7fa6 100%)}
.hero-title{position:absolute;top:220px;width:1200px;text-align:center;color:var(--white);font-size:60px;font-weight:900;letter-spacing:1px}
.hero-sub{position:absolute;top:298px;width:1200px;text-align:center;color:var(--white);font-size:25px;font-weight:700;line-height:38px}
.dots{position:absolute;top:611px;left:561px;display:flex;gap:9px}
.dots span{width:13px;height:13px;border-radius:50%;background:var(--white)}
.dots span.on{background:var(--navy-deep)}

/* section headings */
.sec-title{position:absolute;width:1200px;text-align:center;font-size:30px;font-weight:700;color:var(--heading)}
.sec-bar{position:absolute;left:551px;width:98px;height:4px;background:var(--navy)}

/* welcome */
.frame-corner{position:absolute;border-color:var(--frame);border-style:solid}
.welcome-photo{position:absolute;left:84px;top:932px;width:494px;height:269px;background:linear-gradient(135deg,#b9c4cc 0%,#7d8b98 40%,#2b3a4e 75%,#1f2a3a 100%)}
.welcome-text{position:absolute;left:613px;top:933px;width:505px;font-size:15px;line-height:28.6px;color:var(--text)}
.welcome-text p+p{margin-top:4px}
.btn{position:absolute;display:block;text-align:center;font-weight:700;color:var(--white);text-decoration:none}
.btn-read{left:613px;top:1150px;width:161px;height:43px;line-height:43px;background:var(--navy);font-size:15px}

/* services */
.services-band{position:absolute;left:0;top:1262px;width:1200px;height:585px}
.service{position:absolute;width:360px;text-align:center}
.service-icon{margin:0 auto;width:162px;height:162px;border-radius:50%;background:var(--navy);border:5px solid var(--ring);display:flex;align-items:center;justify-content:center}
.service h3{margin-top:28px;font-size:20px;font-weight:700;color:var(--service-title)}
.service p{margin-top:9px;font-size:15px;line-height:24px;color:var(--muted)}

/* team */
.member{position:absolute;width:260px;text-align:center}
.member-photo{margin:0 auto;width:138px;height:138px;border-radius:50%;border:4px solid var(--ring);background:linear-gradient(180deg,#e9e9e9 0%,#dcd3cb 40%,#c7b3a4 62%,#5d6570 82%,#3e4651 100%)}
.member h4{margin-top:24px;font-size:15px;font-weight:700;color:var(--heading)}
.member p{margin-top:6px;font-size:15px;line-height:20px;color:var(--muted)}
.member-social{margin-top:14px;display:flex;justify-content:center;gap:18px}
.member-social svg{display:block}

/* contact */
.contact{position:absolute;left:0;top:2310px;width:1200px;height:577px;background:linear-gradient(180deg,#1b2c47 0%,#1c2d45 45%,#1d3049 75%,#17283f 100%)}
.contact-title{position:absolute;top:97px;width:1200px;text-align:center;font-size:34px;font-weight:700;color:var(--white)}
.contact-bar{position:absolute;left:551px;top:150px;width:98px;height:4px;background:var(--white)}
.contact-line{position:absolute;width:1200px;display:flex;justify-content:center;gap:28px;font-size:15px;color:var(--white)}
.contact-line span{display:flex;align-items:center;gap:12px}
.field{position:absolute;background:var(--white);border:1px solid #d6d6d6;font-size:14px;color:#555;padding:0 13px;line-height:37px}
.field-select::after{content:"";position:absolute;right:14px;top:13px;width:6px;height:6px;border-right:1.5px solid #666;border-bottom:1.5px solid #666;transform:rotate(45deg)}
.btn-send{left:534px;top:403px;width:131px;height:46px;line-height:46px;background:var(--send);font-size:17px}
.footer-rule{position:absolute;left:0;top:496px;width:1200px;height:1px;background:rgba(255,255,255,.18)}
.copyright{position:absolute;left:74px;top:531px;font-size:11px;color:#d8dde6}
.footer-social{position:absolute;right:73px;top:526px;display:flex;gap:18px}
.footer-social svg{display:block}
</style>
</head>
<body>
<div class="page">

  <header class="site-header">
    <div class="brand"><span class="brand-mark"></span><span class="brand-name">VELMARO</span></div>
    <nav class="nav">
      <a class="active nav-item" style="left:0" href="#">HOME</a>
      <a class="nav-item" style="left:110px" href="#">ABOUT US</a>
      <a class="nav-item" style="left:229px" href="#">SERVICES</a>
      <a class="nav-item" style="left:344px" href="#">TEAM</a>
      <a class="nav-item" style="left:432px" href="#">BLOG</a>
      <a class="nav-item" style="left:519px" href="#">CONTACT</a>
      <span class="nav-item lang" style="left:631px">EN
        <svg width="10" height="8" viewBox="0 0 10 8" style="margin-left:14px"><path d="M1 2l4 4 4-4" fill="none" stroke="#333" stroke-width="1.5"/></svg>
      </span>
    </nav>
  </header>

  <section class="hero" role="img" aria-label="Business people discussing reports with a city skyline overlay">
    <h1 class="hero-title">VELMARO</h1>
    <p class="hero-sub">We help Swiss or European companies wishing to develop<br>their activities in Switzerland.</p>
    <div class="dots"><span class="on"></span><span></span><span></span><span></span></div>
  </section>
  <svg class="abs" style="left:0;top:745px" width="1200" height="40" viewBox="0 0 1200 40">
    <path d="M0 10 Q600 45 1200 6 L1200 40 L0 40 Z" fill="#ffffff"/>
  </svg>

  <section class="welcome">
    <h2 class="sec-title" style="top:842px">WELCOME TO VELMARO</h2>
    <div class="sec-bar" style="top:892px"></div>
    <div class="frame-corner" style="left:75px;top:923px;width:52px;height:55px;border-width:9px 0 0 9px"></div>
    <div class="frame-corner" style="left:535px;top:1154px;width:52px;height:56px;border-width:0 9px 9px 0"></div>
    <div class="welcome-photo" role="img" aria-label="Two businessmen reviewing documents at a laptop in an office"></div>
    <div class="welcome-text">
      <p>Aliquam molestie, mi et imperdiet euismod, dui purus auctor tellus, et &nbsp;interdum lacus lectus et ante. Sed accumsan sollicitudin sapien, sit amet adipiscing turpis gravida ac. In congue, neque ac lobortis volutpat, libero mauris varius mi, &nbsp;vitae suscipit ipsum ligula vitae risus.</p>
      <p>Duis aliquam nibh a dui iaculis viverra id a velit. &nbsp;Aenean a nibh eget turpis vehicula tempus ac sed massa. Vestibulum dolor nulla, ultrices ac tincidunt sed, laoreet non est.</p>
    </div>
    <a class="btn btn-read" href="#">READ MORE</a>
  </section>

  <svg class="abs" style="left:0;top:1262px" width="1200" height="585" viewBox="0 0 1200 585">
    <path d="M0 10 Q600 45 1200 8 L1200 578 Q600 540 0 578 Z" fill="#f1f1f1"/>
  </svg>
  <section class="services-band">
    <h2 class="sec-title" style="top:108px">OUR SERVICES</h2>
    <div class="sec-bar" style="top:165px"></div>
    <div class="service" style="left:60px;top:207px">
      <div class="service-icon">
        <svg width="70" height="70" viewBox="0 0 70 70" fill="none" stroke="#fff" stroke-width="2.2" stroke-linejoin="round" stroke-linecap="round" aria-label="Market research icon" role="img">
          <path d="M6 6h30l8 8v10"/><path d="M6 6v58h24"/>
          <path d="M12 58V48M18 58V42M24 58V46M30 58V50"/><path d="M10 60h26"/>
          <path d="M10 16h14M10 22h10"/>
          <circle cx="44" cy="34" r="12"/><circle cx="44" cy="34" r="7"/>
          <path d="M40 36l3-4 3 3 3-5"/>
          <path d="M52 43l10 12-3 3-10-11"/>
        </svg>
      </div>
      <h3>MARKET RESEARCH</h3>
      <p>Vestibulum ante ipsum primis in faucibus<br>orci luctus et ultrices posuere..</p>
    </div>
    <div class="service" style="left:419px;top:207px">
      <div class="service-icon">
        <svg width="70" height="70" viewBox="0 0 70 70" fill="none" stroke="#fff" stroke-width="2.2" stroke-linejoin="round" stroke-linecap="round" aria-label="Tax representation icon" role="img">
          <path d="M34 58H8V4h24l10 10v14"/><path d="M32 4v10h10"/>
          <path d="M14 20l8-8"/><circle cx="14" cy="12" r="2"/><circle cx="22" cy="20" r="2"/>
          <path d="M14 32h12M14 38h10M14 44h12"/>
          <rect x="34" y="30" width="28" height="36" rx="4"/>
          <rect x="39" y="35" width="18" height="8" rx="1"/>
          <circle cx="41.5" cy="50" r="2.3"/><circle cx="48" cy="50" r="2.3"/><circle cx="54.5" cy="50" r="2.3"/>
          <circle cx="41.5" cy="58" r="2.3"/><circle cx="48" cy="58" r="2.3"/><circle cx="54.5" cy="58" r="2.3"/>
        </svg>
      </div>
      <h3>TAX REPRESENTATION</h3>
      <p>Vestibulum ante ipsum primis in faucibus<br>orci luctus et ultrices posuere..</p>
    </div>
    <div class="service" style="left:779px;top:207px">
      <div class="service-icon">
        <svg width="70" height="70" viewBox="0 0 70 70" fill="none" stroke="#fff" stroke-width="2.2" stroke-linejoin="round" stroke-linecap="round" aria-label="Logistics icon" role="img">
          <path d="M58 64V8"/><path d="M54 64V8"/><circle cx="56" cy="6" r="3"/>
          <path d="M54 12H22"/><path d="M26 12v8"/>
          <path d="M20 26l6-6 6 6z"/>
          <rect x="6" y="30" width="34" height="14"/><path d="M11 34v6M16 34v6M21 34v6M26 34v6M31 34v6M36 34v6"/>
          <rect x="6" y="48" width="34" height="14"/><path d="M11 52v6M16 52v6M21 52v6M26 52v6M31 52v6M36 52v6"/>
          <rect x="42" y="40" width="10" height="10"/><rect x="42" y="52" width="10" height="10"/>
          <path d="M4 64h62"/>
        </svg>
      </div>
      <h3>LOGISTICS</h3>
      <p>Vestibulum ante ipsum primis in faucibus<br>orci luctus et ultrices posuere..</p>
    </div>
  </section>

  <section class="team">
    <h2 class="sec-title" style="top:1874px">OUR TEAM</h2>
    <div class="sec-bar" style="top:1924px"></div>

    <div class="member" style="left:66px;top:1976px">
      <div class="member-photo" role="img" aria-label="Portrait photo of a team member"></div>
      <h4>NAME HEADING</h4>
      <p>Mi et imperdiet euismod, dui purus<br>auctor tellus</p>
      <div class="member-social">
        <svg width="20" height="20" viewBox="0 0 20 20" fill="none" stroke="#8f99a4" stroke-width="2"><rect x="2" y="4" width="16" height="12"/><path d="M2 4l8 7 8-7"/></svg>
        <svg width="20" height="20" viewBox="0 0 20 20" fill="none" stroke="#8f99a4" stroke-width="2" stroke-linecap="round"><path d="M8 12l4-4"/><path d="M9 5l2-2a3.5 3.5 0 0 1 5 5l-2 2"/><path d="M11 15l-2 2a3.5 3.5 0 0 1-5-5l2-2"/></svg>
        <svg width="20" height="20" viewBox="0 0 20 20" fill="#8f99a4"><path d="M5 2l3 4-2 2a10 10 0 0 0 6 6l2-2 4 3-2 3C8 18 2 12 2 4z"/></svg>
      </div>
    </div>
    <div class="member" style="left:335px;top:1976px">
      <div class="member-photo" role="img" aria-label="Portrait photo of a team member"></div>
      <h4>NAME HEADING</h4>
      <p>Mi et imperdiet euismod, dui purus<br>auctor tellus</p>
      <div class="member-social">
        <svg width="20" height="20" viewBox="0 0 20 20" fill="none" stroke="#8f99a4" stroke-width="2"><rect x="2" y="4" width="16" height="12"/><path d="M2 4l8 7 8-7"/></svg>
        <svg width="20" height="20" viewBox="0 0 20 20" fill="none" stroke="#8f99a4" stroke-width="2" stroke-linecap="round"><path d="M8 12l4-4"/><path d="M9 5l2-2a3.5 3.5 0 0 1 5 5l-2 2"/><path d="M11 15l-2 2a3.5 3.5 0 0 1-5-5l2-2"/></svg>
        <svg width="20" height="20" viewBox="0 0 20 20" fill="#8f99a4"><path d="M5 2l3 4-2 2a10 10 0 0 0 6 6l2-2 4 3-2 3C8 18 2 12 2 4z"/></svg>
      </div>
    </div>
    <div class="member" style="left:606px;top:1976px">
      <div class="member-photo" role="img" aria-label="Portrait photo of a team member"></div>
      <h4>NAME HEADING</h4>
      <p>Mi et imperdiet euismod, dui purus<br>auctor tellus</p>
      <div class="member-social">
        <svg width="20" height="20" viewBox="0 0 20 20" fill="none" stroke="#8f99a4" stroke-width="2"><rect x="2" y="4" width="16" height="12"/><path d="M2 4l8 7 8-7"/></svg>
        <svg width="20" height="20" viewBox="0 0 20 20" fill="none" stroke="#8f99a4" stroke-width="2" stroke-linecap="round"><path d="M8 12l4-4"/><path d="M9 5l2-2a3.5 3.5 0 0 1 5 5l-2 2"/><path d="M11 15l-2 2a3.5 3.5 0 0 1-5-5l2-2"/></svg>
        <svg width="20" height="20" viewBox="0 0 20 20" fill="#8f99a4"><path d="M5 2l3 4-2 2a10 10 0 0 0 6 6l2-2 4 3-2 3C8 18 2 12 2 4z"/></svg>
      </div>
    </div>
    <div class="member" style="left:875px;top:1976px">
      <div class="member-photo" role="img" aria-label="Portrait photo of a team member"></div>
      <h4>NAME HEADING</h4>
      <p>Mi et imperdiet euismod, dui purus<br>auctor tellus</p>
      <div class="member-social">
        <svg width="20" height="20" viewBox="0 0 20 20" fill="none" stroke="#8f99a4" stroke-width="2"><rect x="2" y="4" width="16" height="12"/><path d="M2 4l8 7 8-7"/></svg>
        <svg width="20" height="20" viewBox="0 0 20 20" fill="none" stroke="#8f99a4" stroke-width="2" stroke-linecap="round"><path d="M8 12l4-4"/><path d="M9 5l2-2a3.5 3.5 0 0 1 5 5l-2 2"/><path d="M11 15l-2 2a3.5 3.5 0 0 1-5-5l2-2"/></svg>
        <svg width="20" height="20" viewBox="0 0 20 20" fill="#8f99a4"><path d="M5 2l3 4-2 2a10 10 0 0 0 6 6l2-2 4 3-2 3C8 18 2 12 2 4z"/></svg>
      </div>
    </div>
  </section>

  <section class="contact" role="img" aria-label="Night view of an old town waterfront with church towers">
    <svg class="abs" style="left:0;top:0" width="1200" height="40" viewBox="0 0 1200 40">
      <path d="M0 0 L1200 0 L1200 12 Q600 45 0 12 Z" fill="#ffffff"/>
    </svg>
    <h2 class="contact-title">CONTACT US</h2>
    <div class="contact-bar"></div>
    <div class="contact-line" style="top:175px">
      <span><svg width="10" height="14" viewBox="0 0 10 14"><path d="M5 0a5 5 0 0 0-5 5c0 4 5 9 5 9s5-5 5-9a5 5 0 0 0-5-5zm0 7a2 2 0 1 1 0-4 2 2 0 0 1 0 4z" fill="#fff"/></svg>14 Rue des Tilleuls, Neuchâtel, 2000</span>
    </div>
    <div class="contact-line" style="top:204px">
      <span><svg width="13" height="13" viewBox="0 0 13 13"><path d="M3 0l2 3-1.5 1.5a8 8 0 0 0 5 5L10 8l3 2-1.5 3C5 13 0 8 0 1.5Z" fill="#fff"/></svg>+41 32 555 0148</span>
      <span><svg width="15" height="11" viewBox="0 0 15 11"><rect width="15" height="11" fill="#fff"/><path d="M0 0l7.5 6L15 0" fill="none" stroke="#1c2d45" stroke-width="1.3"/></svg>hello@velmaro.ch</span>
    </div>
    <div class="field" style="left:253px;top:248px;width:334px;height:39px">Name</div>
    <div class="field" style="left:253px;top:297px;width:334px;height:39px">Email Address</div>
    <div class="field" style="left:253px;top:345px;width:334px;height:39px">Phone No</div>
    <div class="field field-select" style="left:614px;top:248px;width:333px;height:39px">Subject</div>
    <div class="field" style="left:614px;top:297px;width:333px;height:87px">Message</div>
    <a class="btn btn-send" href="#">SEND</a>
    <div class="footer-rule"></div>
    <p class="copyright">Copyright ©2020 Velmaro SA. All Rights Reserved.</p>
    <div class="footer-social">
      <svg width="22" height="22" viewBox="0 0 20 20" fill="none" stroke="#fff" stroke-width="2"><rect x="2" y="4" width="16" height="12"/><path d="M2 4l8 7 8-7"/></svg>
      <svg width="22" height="22" viewBox="0 0 20 20" fill="#fff"><path d="M5 2l3 4-2 2a10 10 0 0 0 6 6l2-2 4 3-2 3C8 18 2 12 2 4z"/></svg>
      <svg width="22" height="22" viewBox="0 0 20 20" fill="none" stroke="#fff" stroke-width="2" stroke-linecap="round"><path d="M8 12l4-4"/><path d="M9 5l2-2a3.5 3.5 0 0 1 5 5l-2 2"/><path d="M11 15l-2 2a3.5 3.5 0 0 1-5-5l2-2"/></svg>
      <svg width="22" height="22" viewBox="0 0 20 20" fill="#fff"><path d="M10 1a6 6 0 0 0-6 6c0 5 6 12 6 12s6-7 6-12a6 6 0 0 0-6-6zm0 8.5a2.5 2.5 0 1 1 0-5 2.5 2.5 0 0 1 0 5z"/></svg>
      <svg width="22" height="22" viewBox="0 0 20 20" fill="none" stroke="#fff" stroke-width="2" stroke-linecap="round"><circle cx="5" cy="10" r="2.5"/><circle cx="15" cy="4.5" r="2.5"/><circle cx="15" cy="15.5" r="2.5"/><path d="M7.2 8.8l5.6-3M7.2 11.2l5.6 3"/></svg>
    </div>
  </section>

</div>
</body>
</html>
```